New Fun, Positive, energised looking Business Card Needed for High Achiever Coach

I am looking for a two sided full colour business card. I am self employed and have recently re branded my 1-2-1 work re-vitalising high achievers. My target client base for these cards is therefore high achievers - usually aged 40 -55, they are often entrepreneurs, CEO or work in banking and finance and 2/3 are male. I work with them on 90 day or 6 month coaching programs to help them live their success in a healthier, more sustainable and fulfiiled way. They pay for this privately so though they are corporate types the cards need not look 'corporate'. I want to portray the idea of transformation, vitality and re-connecting.
You can get a feel for the look I like on my new website: morvenlisk.co.uk
I want to use this logo with strapline (Re-Vitalising High Achievers) (I purchased off Logoharbor) and font/ colours (the turquoise and green).
Details to include on the card:
www.morvenlisk.co.uk
+44 7915 302618
morven@morvenlisk.co.uk
skype: morvenlisk
I'd also like to include:
Do you struggle to switch off? Want to be healthier and feel fitter? Want closer relationships? More clarity over the direction you are headed? I can help you do these things using integrated mind-body techniques. Visit morvenlisk.co.uk TODAY to apply for a FREE Breakthrough session.
BUT if that is too much text for a card I am open to advice/ammendments.
Updates
Thanks for your design - I am considering them. PLease change the wording to :

```html
<!DOCTYPE html>
<html lang="en">
<head>
<meta charset="utf-8">
<title>Morven Lisk – Business Card</title>
<link rel="stylesheet" href="https://fonts.googleapis.com/css2?family=Open+Sans:wght@400;600;700&display=swap">
<style>
  :root {
    --turquoise: #0fa3c9;
    --green: #5cbb5e;
    --ink: #3a3a3c;
    --metal-light: #eceded;
    --metal-mid: #d6d8d9;
    --metal-dark: #c3c6c8;
    --divider: #8d9194;
    --page: #e9ebee;
  }
  * { box-sizing: border-box; margin: 0; padding: 0; }
  html, body { width: 1200px; height: 987px; overflow: hidden; }
  body {
    background: var(--page);
    font-family: "Open Sans", sans-serif;
    color: var(--ink);
    display: flex;
    flex-direction: column;
    align-items: center;
    justify-content: center;
    gap: 60px;
  }
  .card {
    position: relative;
    width: 700px;
    height: 400px;
    border-radius: 22px;
    overflow: hidden;
    background: linear-gradient(160deg, var(--metal-dark) 0%, var(--metal-light) 40%, var(--metal-mid) 70%, var(--metal-light) 100%);
    box-shadow: 0 6px 18px rgba(0,0,0,0.12);
  }
  .brand {
    position: absolute;
    display: flex;
    align-items: center;
    gap: 12px;
  }
  .brand-dot {
    width: 22px; height: 22px;
    border-radius: 50%;
    background: var(--green);
  }
  .brand-name {
    font-weight: 700;
    font-size: 34px;
    color: var(--turquoise);
    letter-spacing: 0.5px;
    white-space: nowrap;
  }
  .divider {
    position: absolute;
    width: 1.5px;
    background: var(--divider);
  }
  /* front */
  .card--front .brand { left: 50px; top: 115px; }
  .card--front .divider { left: 345px; top: 80px; height: 150px; }
  .footer-band {
    position: absolute;
    left: 0; right: 0; bottom: 0;
    height: 86px;
    background: linear-gradient(90deg, var(--turquoise), #2bb3d4);
    display: flex;
    align-items: center;
    padding-left: 40px;
  }
  .website {
    color: #fff;
    font-size: 20px;
    font-weight: 600;
    letter-spacing: 2px;
  }
  .contacts {
    position: absolute;
    left: 370px; top: 90px;
    list-style: none;
    display: flex;
    flex-direction: column;
    gap: 18px;
    font-size: 21px;
  }
  .contacts li { display: flex; align-items: center; gap: 10px; white-space: nowrap; }
  .contact-icon {
    width: 20px; height: 20px;
    border-radius: 5px;
    background: var(--turquoise);
    display: inline-flex; align-items: center; justify-content: center;
    flex: none;
  }
  /* back */
  .card--back .brand { left: 36px; top: 175px; }
  .card--back .divider { left: 300px; top: 50px; height: 280px; }
  .pitch {
    position: absolute;
    left: 320px; top: 55px; right: 20px;
    font-size: 15px;
    line-height: 1.55;
  }
  .pitch-questions { white-space: nowrap; }
  .pitch p + p { margin-top: 8px; }
  .pitch strong { font-weight: 700; }
</style>
</head>
<body>

  <section class="card card--front" aria-label="Business card front">
    <div class="brand">
      <span class="brand-dot"></span>
      <span class="brand-name">Morven Lisk</span>
    </div>
    <span class="divider"></span>
    <ul class="contacts">
      <li>
        <span class="contact-icon">
          <svg width="12" height="12" viewBox="0 0 24 24" aria-hidden="true"><path d="M6.6 10.8a15 15 0 0 0 6.6 6.6l2.2-2.2a1 1 0 0 1 1-.25 11.4 11.4 0 0 0 3.6.57 1 1 0 0 1 1 1V20a1 1 0 0 1-1 1A17 17 0 0 1 3 4a1 1 0 0 1 1-1h3.5a1 1 0 0 1 1 1c0 1.25.2 2.45.57 3.57a1 1 0 0 1-.25 1z" fill="#fff"/></svg>
        </span>
        +44 7915 302618
      </li>
      <li>
        <span class="contact-icon">
          <svg width="13" height="10" viewBox="0 0 26 20" aria-hidden="true"><rect x="1" y="1" width="24" height="18" rx="2" fill="none" stroke="#fff" stroke-width="2"/><path d="M1 2 L13 11 L25 2" fill="none" stroke="#fff" stroke-width="2"/></svg>
        </span>
        morven@morvenlisk.co.uk
      </li>
      <li>
        <span class="contact-icon"></span>
        morvenlisk
      </li>
    </ul>
    <div class="footer-band" role="img" aria-label="Turquoise decorative band with a thin green accent">
      <p class="website">www.morvenlisk.co.uk</p>
    </div>
  </section>

  <section class="card card--back" aria-label="Business card back">
    <div class="brand">
      <span class="brand-dot"></span>
      <span class="brand-name">Morven Lisk</span>
    </div>
    <span class="divider"></span>
    <div class="pitch">
      <p class="pitch-questions">Do you struggle to switch off?<br>
      Want to be healthier and feel fitter?<br>
      Want closer relationships?<br>
      More clarity over the direction you are headed?</p>
      <p>I can help you do these things using integrated mind-body techniques.</p>
      <p>Visit <strong>morvenlisk.co.uk</strong> TODAY to apply for a FREE Breakthrough session.</p>
    </div>
  </section>

</body>
</html>
```